"BREAKING NEWS!" Fitness photos needed

Hello.... We are creating our new ads for Linkpond and Glimmerly and we need some photos manipulated and text added.

We have 5 photos total that we would like to have the Headline read "Breaking News" and we'll be split testing two different quotes, so I'd like to have:

AD #1:
Breaking News - Finally! Ridgecrest Gets the Gym That Actually Delivers Results (and It's Fun!)

And then a second set on the same photos that read:

AD #2:
Breaking News - Ridgecrest Residents Ditch Boring Workouts for This Life-Changing Fitness Experience

I'd like the photos to pop and stand out, so if color corrections need to be done, please feel free.

I've attached all photos and an example photo that DOES NOT need to be the same. It's just an example I saw that caught my eye, but I feel could be done better.

Thank you!

```html
<!DOCTYPE html>
<html lang="en">
<head>
<meta charset="utf-8">
<title>PulseHaus – Breaking News Ads</title>
<link href="https://fonts.googleapis.com/css2?family=Archivo+Black&family=Noto+Sans:wght@400;500;600&display=swap" rel="stylesheet">
<style>
  :root{
    --stage:#2b2b2b;
    --paper:#ffffff;
    --rule:#e4e4e4;
    --ink:#1c1c1c;
    --muted:#8a8a8a;
    --link-blue:#1f6fd6;
    --caption-bg:#f2f3f5;
    --ad-red:#d10f12;
    --ad-red-dark:#6e0406;
    --ad-yellow:#ffe600;
    --ad-black:#111111;
    --ad-white:#ffffff;
    --ad-grey:#c9c9c9;
    --glimmer:#d62976;
    --linkpond:#1877f2;
  }
  *{box-sizing:border-box;margin:0;padding:0}
  html,body{width:1200px;height:551px;overflow:hidden;background:var(--stage)}
  body{position:relative;font-family:"Noto Sans",sans-serif;color:var(--ink)}

  .frame{position:absolute;background:var(--paper)}
  .panel{position:absolute;background:var(--paper);border:1px solid var(--rule);overflow:hidden}
  .panel > *{position:absolute}

  /* network mark stand-in: dot with name stacked beneath */
  .network{display:flex;flex-direction:column;align-items:center;gap:1px;width:30px;
    font-size:5px;font-weight:600;line-height:1;white-space:nowrap}
  .network .dot{width:10px;height:10px;border-radius:50%}
  .network--glimmerly{color:var(--glimmer)}
  .network--glimmerly .dot{background:var(--glimmer)}
  .network--linkpond{color:var(--linkpond)}
  .network--linkpond .dot{background:var(--linkpond)}

  .account{line-height:1.35;white-space:nowrap}
  .account .name{display:block}
  .account .tag{display:block;color:var(--muted)}
  .account--glimmerly .name{color:var(--ink)}
  .account--linkpond .name{color:var(--link-blue)}
  .account--linkpond .tag{color:#9a9a9a}

  .more{font-weight:600;letter-spacing:1px;line-height:1}

  /* ad artwork */
  .ad-art{container-type:inline-size;overflow:hidden;
    background:radial-gradient(ellipse at 50% 40%, var(--ad-red) 0%, #b00b0d 55%, var(--ad-red-dark) 100%)}
  .ad-photo{position:absolute;left:8%;top:2%;width:88%;height:78%;border-radius:50%;
    background:linear-gradient(160deg,#c9c4bb 0%,#8f8b86 45%,#55545a 100%);
    border-top:2cqw solid var(--ad-yellow);border-right:2cqw solid var(--ad-yellow)}
  .ad-inset{position:absolute;left:4%;bottom:30cqw;width:38%;height:36cqw;border-radius:50%;
    background:linear-gradient(150deg,#d6d2cb 0%,#8e8a85 60%,#5a585c 100%);
    border-top:1.6cqw solid var(--ad-yellow);border-left:1.6cqw solid var(--ad-yellow)}
  .ad-live{position:absolute;left:53%;bottom:25.5cqw;width:34%;height:6.8cqw;background:var(--ad-yellow);
    transform:skewX(-18deg);display:flex;align-items:center;justify-content:center;
    font-family:"Archivo Black",sans-serif;font-style:italic;font-size:6cqw;color:var(--ad-black);line-height:1}
  .ad-live span{transform:skewX(18deg)}
  .ad-headline{position:absolute;left:3%;bottom:14.5cqw;width:95%;height:11cqw;display:flex;
    transform:skewX(-12deg);border:0.6cqw solid var(--ad-white);
    font-family:"Archivo Black",sans-serif;font-style:italic;font-size:8.2cqw;line-height:1}
  .ad-headline .breaking{flex:0 0 61%;background:var(--ad-red);color:var(--ad-white);display:flex;align-items:center;justify-content:center}
  .ad-headline .news{flex:1;background:var(--ad-black);color:var(--ad-white);display:flex;align-items:center;justify-content:center}
  .ad-headline span span{transform:skewX(12deg)}
  .ad-quote{position:absolute;left:1.5%;bottom:3.4cqw;width:96%;height:11cqw;background:var(--ad-white);
    transform:skewX(-12deg);display:flex;align-items:center;justify-content:center;
    font-family:"Archivo Black",sans-serif;font-style:italic;font-size:4.1cqw;line-height:1.08;color:var(--ad-black);text-align:center}
  .ad-quote p{transform:skewX(12deg)}
  .ad-stripe{position:absolute;left:52%;bottom:0.6cqw;width:45%;height:2.4cqw;background:var(--ad-grey);transform:skewX(-12deg)}

  /* glimmerly footer */
  .icon{width:11px;height:11px;fill:none;stroke:var(--ink);stroke-width:1.6;stroke-linejoin:round;stroke-linecap:round}
  .meta{font-size:7.6px;line-height:1;white-space:nowrap}
  .meta--muted{color:var(--muted)}

  /* linkpond caption */
  .caption{left:0;right:0;background:var(--caption-bg)}
  .caption .brand{position:absolute;left:3px;font-size:6.4px;color:#777;letter-spacing:.1px}
  .caption .line{position:absolute;left:3px;font-size:7.4px;color:var(--ink)}
  .cta{position:absolute;display:flex;align-items:center;justify-content:center;font-size:5.6px;color:var(--ink);border-radius:2px}
  .cta--outline{border:1px solid #8a8a8a;background:var(--paper)}
  .cta--fill{background:#e3e4e6}
  .reactions{left:4px;right:4px;display:flex;justify-content:space-between;align-items:center;font-size:7.6px;color:#606060}
  .reactions .count{display:flex;align-items:center;gap:3px}
  .like-badge{width:10px;height:10px;border-radius:50%;background:var(--link-blue)}
  .divider{left:4px;right:4px;height:1px;background:var(--rule)}
  .action{display:flex;align-items:center;gap:3px;font-size:7.8px;color:#606060;transform:translateY(-50%);white-space:nowrap}
  .action svg{width:10px;height:10px;fill:none;stroke:#606060;stroke-width:1.5;stroke-linejoin:round}
</style>
</head>
<body>

<!-- Glimmerly small -->
<div class="frame" style="left:51px;top:129px;width:190px;height:299px"></div>
<section class="panel" style="left:56px;top:133px;width:180px;height:286px">
  <div class="network network--glimmerly" style="left:3px;top:10px"><span class="dot"></span>Glimmerly</div>
  <div class="account account--glimmerly" style="left:37px;top:9px;font-size:6.6px"><span class="name">PulseHaus</span><span class="tag">Sponsored</span></div>
  <div class="more" style="left:161px;top:13px;font-size:8px">•••</div>
  <div class="ad-art" style="left:0;top:36px;width:180px;height:180px" role="img" aria-label="Red halftone background with circular photos of women exercising in a gym">
    <div class="ad-photo"></div><div class="ad-inset"></div>
    <div class="ad-live"><span>LIVE ///</span></div>
    <div class="ad-headline"><span class="breaking"><span>BREAKING</span></span><span class="news"><span>NEWS</span></span></div>
    <div class="ad-quote"><p>Finally! Ridgecrest Gets the Gym That<br>Actually Delivers Results (and It's Fun!)</p></div>
    <div class="ad-stripe"></div>
  </div>
  <svg class="icon" style="left:10px;top:222px" viewBox="0 0 24 24"><path d="M12 21s-8-5.5-8-11a4.5 4.5 0 0 1 8-2.8A4.5 4.5 0 0 1 20 10c0 5.5-8 11-8 11z"/></svg>
  <svg class="icon" style="left:32px;top:222px" viewBox="0 0 24 24"><path d="M20 12a8 8 0 1 1-3-6.2A8 8 0 0 1 20 12l1 8-5-3"/></svg>
  <svg class="icon" style="left:54px;top:222px" viewBox="0 0 24 24"><path d="M3 4h18L12 21l-2-9zM10 12l11-8"/></svg>
  <svg class="icon" style="left:160px;top:222px" viewBox="0 0 24 24"><path d="M6 3h12v18l-6-5-6 5z"/></svg>
  <div class="meta" style="left:9px;top:240px">110 likes</div>
  <div class="meta" style="left:9px;top:253px">PulseHaus</div>
  <div class="meta meta--muted" style="left:9px;top:266px">View all 8 comments</div>
</section>

<!-- Glimmerly large -->
<div class="frame" style="left:279px;top:85px;width:290px;height:396px"></div>
<section class="panel" style="left:284px;top:91px;width:279px;height:382px">
  <div class="network network--glimmerly" style="left:3px;top:11px"><span class="dot"></span>Glimmerly</div>
  <div class="account account--glimmerly" style="left:37px;top:10px;font-size:6.6px"><span class="name">PulseHaus</span><span class="tag">Sponsored</span></div>
  <div class="more" style="left:258px;top:14px;font-size:8px">•••</div>
  <div class="ad-art" style="left:2px;top:37px;width:276px;height:276px" role="img" aria-label="Red halftone background with circular photos of women exercising in a gym">
    <div class="ad-photo"></div><div class="ad-inset"></div>
    <div class="ad-live"><span>LIVE ///</span></div>
    <div class="ad-headline"><span class="breaking"><span>BREAKING</span></span><span class="news"><span>NEWS</span></span></div>
    <div class="ad-quote"><p>Finally! Ridgecrest Gets the Gym That<br>Actually Delivers Results (and It's Fun!)</p></div>
    <div class="ad-stripe"></div>
  </div>
  <svg class="icon" style="left:10px;top:319px" viewBox="0 0 24 24"><path d="M12 21s-8-5.5-8-11a4.5 4.5 0 0 1 8-2.8A4.5 4.5 0 0 1 20 10c0 5.5-8 11-8 11z"/></svg>
  <svg class="icon" style="left:32px;top:319px" viewBox="0 0 24 24"><path d="M20 12a8 8 0 1 1-3-6.2A8 8 0 0 1 20 12l1 8-5-3"/></svg>
  <svg class="icon" style="left:55px;top:319px" viewBox="0 0 24 24"><path d="M3 4h18L12 21l-2-9zM10 12l11-8"/></svg>
  <svg class="icon" style="left:257px;top:319px" viewBox="0 0 24 24"><path d="M6 3h12v18l-6-5-6 5z"/></svg>
  <div class="meta" style="left:9px;top:338px">110 likes</div>
  <div class="meta" style="left:9px;top:352px">PulseHaus</div>
  <div class="meta meta--muted" style="left:9px;top:365px">View all 8 comments</div>
</section>

<!-- Linkpond small -->
<div class="frame" style="left:627px;top:100px;width:189px;height:295px"></div>
<section class="panel" style="left:631px;top:104px;width:181px;height:287px">
  <div class="network network--linkpond" style="left:3px;top:12px"><span class="dot"></span>Linkpond</div>
  <div class="account account--linkpond" style="left:38px;top:9px;font-size:7.4px"><span class="name">PulseHaus</span><span class="tag">Sponsored</span></div>
  <div class="ad-art" style="left:1px;top:50px;width:179px;height:145px" role="img" aria-label="Red halftone background with circular photos of women exercising in a gym">
    <div class="ad-photo"></div><div class="ad-inset" style="bottom:28cqw;height:30cqw;width:32%"></div>
    <div class="ad-live" style="bottom:23cqw"><span>LIVE ///</span></div>
    <div class="ad-headline" style="bottom:13cqw;height:10cqw"><span class="breaking"><span>BREAKING</span></span><span class="news"><span>NEWS</span></span></div>
    <div class="ad-quote" style="bottom:2cqw;height:10cqw"><p>Finally! Ridgecrest Gets the Gym That<br>Actually Delivers Results (and It's Fun!)</p></div>
  </div>
  <div class="caption" style="top:195px;height:45px">
    <span class="brand" style="top:7px">PULSEHAUS</span>
    <span class="line" style="top:18px">Be fit stay Fit!</span>
    <span class="cta cta--outline" style="left:127px;top:16px;width:47px;height:13px">DOWNLOAD</span>
  </div>
  <div class="reactions" style="top:245px"><span class="count"><span class="like-badge"></span>25</span><span>5 Comments</span></div>
  <div class="divider" style="top:263px"></div>
  <div class="action" style="left:20px;top:276px"><svg viewBox="0 0 24 24"><path d="M7 10v11H3V10zM7 10l4-8a3 3 0 0 1 3 3v4h6a2 2 0 0 1 2 2l-2 8a2 2 0 0 1-2 2H7"/></svg>Like</div>
  <div class="action" style="left:64px;top:276px"><svg viewBox="0 0 24 24"><path d="M3 4h18v13H9l-5 4v-4H3z"/></svg>Comment</div>
  <div class="action" style="left:128px;top:276px"><svg viewBox="0 0 24 24"><path d="M14 4l8 7-8 7v-4c-6 0-9 2-12 6 1-7 5-11 12-12z"/></svg>Share</div>
</section>

<!-- Linkpond large -->
<div class="frame" style="left:859px;top:83px;width:285px;height:375px"></div>
<section class="panel" style="left:862px;top:86px;width:278px;height:366px">
  <div class="network network--linkpond" style="left:2px;top:10px"><span class="dot"></span>Linkpond</div>
  <div class="account account--linkpond" style="left:38px;top:7px;font-size:7.4px"><span class="name">PulseHaus</span><span class="tag">Sponsored</span></div>
  <div class="ad-art" style="left:2px;top:49px;width:273px;height:216px" role="img" aria-label="Red halftone background with circular photos of women exercising in a gym">
    <div class="ad-photo"></div><div class="ad-inset" style="bottom:28cqw;height:33cqw;width:34%"></div>
    <div class="ad-live" style="bottom:24cqw"><span>LIVE ///</span></div>
    <div class="ad-headline" style="bottom:13.5cqw;height:10.5cqw"><span class="breaking"><span>BREAKING</span></span><span class="news"><span>NEWS</span></span></div>
    <div class="ad-quote" style="bottom:2.5cqw;height:10.5cqw"><p>Finally! Ridgecrest Gets the Gym That<br>Actually Delivers Results (and It's Fun!)</p></div>
    <div class="ad-stripe" style="bottom:0"></div>
  </div>
  <div class="caption" style="top:265px;height:53px">
    <span class="brand" style="top:10px">PULSEHAUS</span>
    <span class="line" style="top:24px">Be fit stay Fit!</span>
    <span class="cta cta--fill" style="left:217px;top:19px;width:51px;height:19px;font-size:6.8px">Download</span>
  </div>
  <div class="reactions" style="top:324px"><span class="count"><span class="like-badge"></span>25</span><span>5 Comments</span></div>
  <div class="divider" style="top:342px"></div>
  <div class="action" style="left:35px;top:354px"><svg viewBox="0 0 24 24"><path d="M7 10v11H3V10zM7 10l4-8a3 3 0 0 1 3 3v4h6a2 2 0 0 1 2 2l-2 8a2 2 0 0 1-2 2H7"/></svg>Like</div>
  <div class="action" style="left:113px;top:354px"><svg viewBox="0 0 24 24"><path d="M3 4h18v13H9l-5 4v-4H3z"/></svg>Comment</div>
  <div class="action" style="left:208px;top:354px"><svg viewBox="0 0 24 24"><path d="M14 4l8 7-8 7v-4c-6 0-9 2-12 6 1-7 5-11 12-12z"/></svg>Share</div>
</section>

</body>
</html>
```